Glen Whitmore Professional Coaching

I would like a website with a mountain theme geared towards professional executives reaching higher peaks and goals. This is a 3 page website with brand essence information on the opening page, the coaching process on a second page and "about me" and lead capture form on a third page

Target Market(s)

C-Level audience, involved in tech, government, manufacturing, and transportation type of corporations

Coding

Coded - Design and coding required

Number of Pages Required

3 page

Font styles to use
Sans Serif

Colors
a7a7a7
1b1b1b
e8e8e8
3176b5
abd036
0355a3

Requirements
Must have
• Looking for a user friendly site that I can manage/update going forward. Must have:
• 1. "Is coaching right for you?" - page 1
• 2. "Our Process" page 2 - I will describe how we approach coaching
• 3. "Contact us" page 3 where I can capture contact information from potential clients
• 4. Clean and professional with more modern font
• 5. Links to personal social media sites
• 6. Ability to upload/download .pdf documents as resources
• 7. Ability to add on new pages in the future (such as a blog page)
Nice to have
• I want a place to store articles I write or use.
• LinkedIn or Twitter Feed
Should not have
• Not fluffy or too 'zen' like personal life coaches tend to present.

```html
<!DOCTYPE html>
<html lang="en">
<head>
<meta charset="utf-8">
<title>Glen Whitmore Professional Coaching</title>
<link href="https://fonts.googleapis.com/css2?family=Raleway:wght@400;500;600;700&family=Open+Sans:ital,wght@0,400;0,600;0,700;1,400;1,600&display=swap" rel="stylesheet">
<style>
  :root {
    --ink: #1b1b1b;
    --grey: #a7a7a7;
    --text-grey: #6a6a6a;
    --light: #e8e8e8;
    --blue: #3176b5;
    --navy: #0d3f7e;
    --deep: #0355a3;
    --accent: #e0811e;
    --white: #ffffff;
  }
  * { margin: 0; padding: 0; box-sizing: border-box; }
  html, body { width: 1200px; height: 3169px; overflow: hidden; }
  body {
    position: relative;
    background: var(--white);
    font-family: "Open Sans", Arial, sans-serif;
    color: var(--ink);
  }
  .abs { position: absolute; }

  /* Hero */
  .hero-scene {
    position: absolute; left: 0; top: 0; width: 1200px; height: 880px;
    background:
      linear-gradient(180deg, rgba(255,255,255,0) 0%, rgba(255,255,255,0) 62%, rgba(255,255,255,0.7) 82%, #fff 100%),
      linear-gradient(180deg, #4f82c4 0%, #6f97cc 18%, #8aa3c8 32%, #5a6f98 50%, #6e86b4 64%, #a9bbd8 78%, #e4ebf4 100%);
  }
  .brand { left: 112px; top: 20px; font-family: "Raleway", sans-serif; font-weight: 500; font-size: 31px; color: var(--white); }
  .main-nav a { position: absolute; top: 30px; font-size: 16px; color: var(--white); text-decoration: none; }
  .hero-title {
    left: 0; width: 1200px; top: 152px; text-align: center;
    font-family: "Raleway", sans-serif; font-weight: 700; font-size: 71px; line-height: 72px; color: var(--white);
  }
  .hero-title .quote { color: var(--accent); font-family: Georgia, serif; font-size: 62px; vertical-align: 10px; }
  .slider-dots { left: 548px; top: 589px; display: flex; gap: 15px; }
  .slider-dots span { width: 14px; height: 14px; border-radius: 50%; border: 2px solid var(--white); }
  .slider-dots span.active { background: var(--white); }

  /* Section tags */
  .section-tag { width: 132px; height: 96px; }
  .section-tag span {
    position: absolute; left: 0; width: 132px; top: 38px; text-align: center;
    font-size: 13px; color: #777;
  }

  /* About */
  .about-heading { left: 112px; top: 893px; font-family: "Raleway", sans-serif; font-weight: 500; font-size: 51px; color: var(--ink); }
  .about-copy { left: 112px; top: 978px; width: 400px; font-size: 14.5px; line-height: 31px; color: var(--text-grey); }
  .btn-read {
    left: 112px; top: 1204px; width: 166px; height: 51px; border-radius: 26px;
    background: var(--navy); color: var(--white); font-weight: 700; font-size: 15.5px;
    display: flex; align-items: center; justify-content: center; letter-spacing: 0.3px;
  }

  /* Process */
  .section-heading { left: 0; width: 1200px; text-align: center; font-family: "Raleway", sans-serif; font-weight: 500; font-size: 51px; color: var(--ink); }
  .process-scene {
    left: 0; top: 1640px; width: 500px; height: 380px;
    background: radial-gradient(ellipse 60% 55% at 30% 55%, #b69c85 0%, #cdb9a6 35%, #e6ddd4 60%, rgba(255,255,255,0) 100%);
  }
  .step { width: 300px; text-align: center; }
  .step-circle {
    position: absolute; width: 136px; height: 136px; border-radius: 50%; background: var(--white);
    box-shadow: 0 4px 18px rgba(0,0,0,0.12);
  }
  .step-circle svg { position: absolute; left: 34px; top: 34px; }
  .step-title { position: absolute; left: 0; width: 300px; top: 0; font-family: "Raleway", sans-serif; font-size: 22px; color: var(--ink); }
  .step-text { position: absolute; left: 0; width: 300px; top: 40px; font-size: 16px; line-height: 26px; color: #333; }

  /* Blog */
  .blog-card {
    width: 312px; height: 250px; background: var(--white);
    box-shadow: 0 2px 14px rgba(0,0,0,0.12);
  }
  .blog-card h3 { position: absolute; left: 25px; top: 48px; font-size: 18px; font-weight: 700; color: var(--ink); }
  .blog-card p { position: absolute; left: 25px; top: 86px; width: 264px; font-size: 13px; line-height: 25.5px; color: #444; }
  .blog-card hr { position: absolute; left: 25px; top: 184px; width: 262px; border: 0; border-top: 1px solid var(--light); }
  .blog-card .avatar { position: absolute; left: 25px; top: 203px; width: 30px; height: 30px; border-radius: 50%; background: linear-gradient(135deg, #c98d6c, #7a4a38); }
  .blog-card .author { position: absolute; left: 76px; top: 207px; font-style: italic; font-weight: 600; font-size: 16px; color: var(--deep); }
  .blog-card .date { position: absolute; right: 25px; top: 211px; font-size: 11px; color: var(--ink); }

  /* Footer */
  .footer-scene {
    left: 0; top: 2450px; width: 1200px; height: 719px;
    background: linear-gradient(180deg, #ffffff 0%, #eaf2fb 12%, #bcd5ee 28%, #dbe8f6 42%, #9fc1e6 62%, #4d86c6 74%, #1f4f8c 84%, #0f2f5a 100%);
  }
  .footer-panel { left: 112px; top: 2662px; width: 976px; height: 290px; background: rgba(255,255,255,0.82); }
  .footer-heading { font-family: "Raleway", sans-serif; font-weight: 700; font-size: 20px; color: var(--navy); }
  .footer-links a, .contact-line { position: absolute; font-size: 14.5px; color: #333; text-decoration: none; white-space: nowrap; }
  .contact-line svg { position: absolute; left: 0; top: 4px; }
  .contact-line span { padding-left: 20px; }
  .email-field {
    left: 602px; top: 2734px; width: 328px; height: 44px; background: var(--white); border: 1px solid #cfd6de;
    font-size: 14px; color: #666; padding: 13px 14px;
  }
  .btn-subscribe {
    left: 930px; top: 2734px; width: 129px; height: 44px; background: var(--navy); color: var(--white);
    font-size: 14.5px; letter-spacing: 1px; display: flex; align-items: center; justify-content: center;
  }
  .social a { position: absolute; top: 2806px; width: 38px; height: 38px; border-radius: 50%; background: var(--white); box-shadow: 0 1px 6px rgba(0,0,0,0.12); }
  .social a::after { content: ""; position: absolute; left: 15px; top: 15px; width: 8px; height: 8px; border-radius: 50%; background: var(--navy); }
  .copyright { left: 0; width: 1200px; top: 3094px; text-align: center; font-size: 14px; color: var(--white); }
</style>
</head>
<body>

<!-- Hero -->
<div class="hero-scene" role="img" aria-label="Photograph of snow-covered mountain range under a blue sky"></div>
<div class="abs brand">Glen Whitmore</div>
<nav class="main-nav">
  <a href="#" style="left:625px">Home</a>
  <a href="#" style="left:714px">About Me</a>
  <a href="#" style="left:832px">Coaching Process</a>
  <a href="#" style="left:1008px">Contact Us</a>
</nav>
<h1 class="abs hero-title"><span class="quote">&#8220;</span>Glen Whitmore<br>professional coaching<span class="quote">&#8221;</span></h1>
<div class="abs slider-dots"><span class="active"></span><span></span><span></span><span></span></div>

<!-- About -->
<div class="abs section-tag" style="left:534px;top:810px">
  <svg width="132" height="96" viewBox="0 0 132 96"><rect x="43" y="25" width="46" height="46" transform="rotate(45 66 48)" fill="#fff" stroke="#9a9a9a" stroke-width="1.2"/></svg>
  <span>About Me</span>
</div>
<h2 class="abs about-heading">About Me</h2>
<p class="abs about-copy">Lorem ipsum dolor sit amet, consectetur adipiscing elit, sed do eiusmod tempor incididunt ut labore et dolore magna aliqua. Ut enim ad minim veniam, quis nostrud exercitation ullamco laboris nisi ut aliquip ex ea commodo consequat. Duis aute irure dolor in reprehenderit in voluptate velit esse cillum dolore eu fugiat nulla pariatur</p>
<a class="abs btn-read">READ MORE</a>

<svg class="abs" style="left:590px;top:850px" width="500" height="460" viewBox="0 0 500 460">
  <defs>
    <linearGradient id="portraitTone" x1="0" y1="0" x2="1" y2="1">
      <stop offset="0" stop-color="#4f7a3a"/>
      <stop offset="0.5" stop-color="#6f8f5a"/>
      <stop offset="1" stop-color="#2b3f66"/>
    </linearGradient>
    <filter id="soft" x="-20%" y="-20%" width="140%" height="140%"><feDropShadow dx="0" dy="6" stdDeviation="8" flood-opacity="0.18"/></filter>
  </defs>
  <polygon points="218,50 440,272 218,494 -4,272" transform="translate(0,-30)" fill="#8c9ab4"/>
  <polygon points="253,8 475,230 253,452 31,230" fill="#fff" filter="url(#soft)"/>
  <polygon points="253,22 461,230 253,438 45,230" fill="url(#portraitTone)" role="img" aria-label="Portrait photograph of the coach outdoors"/>
</svg>

<!-- Process -->
<div class="abs section-tag" style="left:534px;top:1398px">
  <svg width="132" height="96" viewBox="0 0 132 96"><rect x="43" y="25" width="46" height="46" transform="rotate(45 66 48)" fill="#fff" stroke="#9a9a9a" stroke-width="1.2"/></svg>
  <span>Process</span>
</div>
<h2 class="abs section-heading" style="top:1515px">Coaching Process</h2>
<div class="abs process-scene" role="img" aria-label="Illustration of a sunlit mountain peak"></div>

<svg class="abs" style="left:330px;top:1660px" width="540" height="80" viewBox="0 0 540 80" fill="none" stroke="#b8b8b8" stroke-width="3" stroke-dasharray="8 7">
  <path d="M6 48 C40 10, 90 20, 120 40 S 160 50, 168 40"/>
  <path d="M160 30 L170 40 L158 48" stroke-dasharray="none"/>
  <path d="M374 48 C408 10, 458 20, 488 40 S 528 50, 536 40"/>
  <path d="M528 30 L538 40 L526 48" stroke-dasharray="none"/>
</svg>

<div class="abs step-circle" style="left:167px;top:1622px">
  <svg width="68" height="68" viewBox="0 0 68 68" fill="none" stroke="#1c4f8f" stroke-width="3">
    <circle cx="34" cy="26" r="22"/><ellipse cx="34" cy="26" rx="10" ry="22"/><path d="M12 26h44M16 14h36M16 38h36"/>
    <circle cx="34" cy="40" r="7" fill="#1c4f8f"/><path d="M20 66c0-10 6-16 14-16s14 6 14 16z" fill="#1c4f8f"/>
  </svg>
</div>
<div class="abs step-circle" style="left:532px;top:1622px">
  <svg width="68" height="68" viewBox="0 0 68 68" fill="#1c4f8f">
    <circle cx="16" cy="16" r="6"/><circle cx="34" cy="12" r="7"/><circle cx="52" cy="16" r="6"/>
    <path d="M6 44c0-12 4-20 10-20s10 8 10 20z"/><path d="M42 44c0-12 4-20 10-20s10 8 10 20z"/>
    <path d="M22 50c0-16 5-28 12-28s12 12 12 28z"/>
    <path d="M6 56 Q34 68 62 56" fill="none" stroke="#1c4f8f" stroke-width="3"/>
  </svg>
</div>
<div class="abs step-circle" style="left:898px;top:1622px">
  <svg width="68" height="68" viewBox="0 0 68 68" fill="none" stroke="#1c4f8f" stroke-width="3">
    <circle cx="34" cy="22" r="18"/><ellipse cx="34" cy="22" rx="8" ry="18"/><path d="M16 22h36"/>
    <circle cx="14" cy="44" r="5" fill="#1c4f8f"/><circle cx="54" cy="44" r="5" fill="#1c4f8f"/>
    <path d="M6 66c0-9 3-14 8-14s8 5 8 9l12-4 12 4c0-4 3-9 8-9s8 5 8 14z" fill="#1c4f8f"/>
  </svg>
</div>

<div class="abs step" style="left:85px;top:1785px">
  <div class="step-title">Sed ut perspiciatis unde</div>
  <div class="step-text">Lorem ipsum dolor sit amet,<br>consectetur adipiscing elit, sed do</div>
</div>
<div class="abs step" style="left:450px;top:1785px">
  <div class="step-title">Sed ut perspiciatis unde</div>
  <div class="step-text">Lorem ipsum dolor sit amet,<br>consectetur adipiscing elit, sed do</div>
</div>
<div class="abs step" style="left:816px;top:1785px">
  <div class="step-title">Sed ut perspiciatis unde</div>
  <div class="step-text">Lorem ipsum dolor sit amet,<br>consectetur adipiscing elit, sed do</div>
</div>

<!-- Blog -->
<div class="abs section-tag" style="left:534px;top:2020px">
  <svg width="132" height="96" viewBox="0 0 132 96"><rect x="43" y="25" width="46" height="46" transform="rotate(45 66 48)" fill="#fff" stroke="#9a9a9a" stroke-width="1.2"/></svg>
  <span>News</span>
</div>
<h2 class="abs section-heading" style="top:2130px">Our Blog</h2>

<div class="abs footer-scene" role="img" aria-label="Illustration of snowy blue mountains with a pine forest along the bottom"></div>

<article class="abs blog-card" style="left:110px;top:2240px">
  <h3>Perspiciatis</h3>
  <p>At vero eos et accusamus et iusto odio mos mus qui blanditiis praesentium tatum del-eniti atque corrupti quos dolores et</p>
  <hr><div class="avatar" role="img" aria-label="Author photo"></div>
  <span class="author">Nora Field</span><span class="date">28,oct 2018</span>
</article>
<article class="abs blog-card" style="left:446px;top:2240px">
  <h3>Perspiciatis</h3>
  <p>At vero eos et accusamus et iusto odio mos mus qui blanditiis praesentium tatum del-eniti atque corrupti quos dolores et</p>
  <hr><div class="avatar" role="img" aria-label="Author photo"></div>
  <span class="author">Nora Field</span><span class="date">28,oct 2018</span>
</article>
<article class="abs blog-card" style="left:782px;top:2240px">
  <h3>Perspiciatis</h3>
  <p>At vero eos et accusamus et iusto odio mos mus qui blanditiis praesentium tatum del-eniti atque corrupti quos dolores et</p>
  <hr><div class="avatar" role="img" aria-label="Author photo"></div>
  <span class="author">Nora Field</span><span class="date">28,oct 2018</span>
</article>

<!-- Footer -->
<div class="abs footer-panel"></div>
<div class="abs footer-heading" style="left:164px;top:2728px">NAVIGATE</div>
<nav class="footer-links">
  <a href="#" style="left:165px;top:2773px">Home</a>
  <a href="#" style="left:165px;top:2805px">About Me</a>
  <a href="#" style="left:165px;top:2836px">Process</a>
  <a href="#" style="left:165px;top:2868px">Contact Us</a>
</nav>
<div class="abs footer-heading" style="left:334px;top:2728px">CONTACT US</div>
<div class="contact-line" style="left:334px;top:2773px">
  <svg width="13" height="13" viewBox="0 0 13 13"><rect width="13" height="13" rx="2" fill="#0d3f7e"/><path d="M4 3l1.6 1.8-1 1c.6 1.2 1.4 2 2.6 2.6l1-1L10 9l-1 1.4C6 10 3 7 2.8 4z" fill="#fff"/></svg>
  <span>1300 555 014</span>
</div>
<div class="contact-line" style="left:334px;top:2798px">
  <svg width="13" height="13" viewBox="0 0 13 13"><rect width="13" height="13" rx="2" fill="#0d3f7e"/><rect x="3" y="4" width="7" height="5" fill="none" stroke="#fff" stroke-width="1.2"/><path d="M3 4l3.5 3L10 4" fill="none" stroke="#fff" stroke-width="1.2"/></svg>
  <span>info@glenwhitmore.com</span>
</div>
<div class="abs email-field">Enter Your Email Address</div>
<div class="abs btn-subscribe">SUBSCRIBE</div>
<div class="social">
  <a href="#" aria-label="Social profile one" style="left:602px"></a>
  <a href="#" aria-label="Social profile two" style="left:649px"></a>
  <a href="#" aria-label="Social profile three" style="left:695px"></a>
  <a href="#" aria-label="Social profile four" style="left:744px"></a>
</div>
<div class="abs copyright">&copy;Copyrights 2019.The Company Name All Rights Reserved</div>

</body>
</html>
```